Sales presentation introduction for Finance and Tech firms

Our business is two fold - 1) recruitment 2) consultancy. We would like a one or two page template that we can use to send to potential clients. The template will ideally be the same for the recruitment and consultancy side. We need to be able to edit the template to enter text.

I have attached our logo so you can see what we currently use on Corvella.

Sector is financial services and technology. We do not intent to have lots of text but the layout/images/designs to be used should cover some of page in a way that it takes up some space to avoid having to write lot of text.

Open to colour suggestions.

Please look at the attached word doc to see the text I would like for the two presentations.

Happy to answer questions.

Target Market(s)

Directors

Industry/Entity Type

Finance and tech companies

Colors
0094D4
00A9DD
6FCCEA
C7EBF8
E9F6FB

Requirements
Must have
• Editable text

```html
<!DOCTYPE html>
<html lang="en">
<head>
<meta charset="utf-8">
<title>Veltrane – Consultancy and Recruitment</title>
<link href="https://fonts.googleapis.com/css2?family=Oswald:wght@400;500;600&family=Roboto+Condensed:wght@400;700&display=swap" rel="stylesheet">
<style>
:root{
  --ink:#2b2a31;
  --navy:#1b4f92;
  --blue:#1f6fbf;
  --bright:#0094d4;
  --sky:#6fccea;
  --pale:#c7ebf8;
  --mist:#e9f6fb;
  --grey:#5b5b60;
  --text:#55565b;
  --bg:#e4e4e6;
}
*{margin:0;padding:0;box-sizing:border-box}
html,body{width:677px;height:1200px;overflow:hidden;background:var(--bg)}
body{position:relative;font-family:"Roboto Condensed",sans-serif;color:var(--text)}
.page{position:absolute;left:128px;width:420px;height:585px;background:#fff;overflow:hidden;box-shadow:0 2px 6px rgba(0,0,0,.18)}
.page--consultancy{top:10px}
.page--recruitment{top:605px}
.abs{position:absolute}
.hero-photo{left:150px;top:0;width:270px;height:135px;background:linear-gradient(120deg,#8a97a6 0%,#c9d2dc 45%,#e8edf2 70%,#9fb1c4 100%)}
.band{left:0;top:0;width:420px}
.brand{display:flex;align-items:center;gap:6px;font-family:"Oswald",sans-serif;font-weight:400;color:var(--grey);letter-spacing:.5px}
.brand-mark{width:12px;height:12px;background:var(--bright)}
.brand--light{color:#fff}
.tagline{left:10px;top:118px;width:200px;color:#fff;font-size:7.6px;line-height:9px}
.phone{font-family:"Oswald",sans-serif;font-weight:500;color:#fff;font-size:15px}
.heading{font-family:"Oswald",sans-serif;font-weight:500;color:var(--navy);font-size:12px;letter-spacing:.2px}
.small{font-size:4.6px;line-height:6px;color:var(--text)}
.services{left:10px;top:292px;width:400px;display:flex;justify-content:space-between}
.service{width:40px;text-align:center;font-size:3.8px;line-height:4.6px;color:var(--ink)}
.service-dot{width:24px;height:24px;margin:0 auto 3px;border-radius:50%;background:var(--blue);border:1.5px solid var(--sky);display:flex;align-items:center;justify-content:center}
.service-dot svg{width:12px;height:12px}
.section{width:190px}
.section h3{font-family:"Oswald",sans-serif;font-weight:500;color:var(--navy);font-size:11px;display:flex;align-items:center;gap:4px;margin-bottom:5px}
.section h3::before{content:"";width:7px;height:7px;border-radius:50%;background:var(--blue);box-shadow:0 0 0 1px var(--sky)}
.web-bar{left:0;top:538px;width:420px}
.web{left:12px;top:542px;font-family:"Roboto Condensed",sans-serif;color:#fff;font-size:11px;letter-spacing:2px}
.contact{right:12px;top:566px;font-family:"Oswald",sans-serif;font-size:8.6px;color:var(--ink);display:flex;align-items:center;gap:4px}
.contact-dot{width:8px;height:8px;background:var(--bright)}
.intro{left:12px;top:120px;width:396px;font-size:8px;line-height:9px;color:var(--ink)}
.pill{left:42px;top:258px;width:336px;height:30px;border-radius:15px;background:linear-gradient(90deg,var(--navy),var(--blue));border:1px solid var(--sky);color:#fff;font-size:6.6px;font-weight:700;line-height:9px;text-align:center;padding-top:5px}
.ticks{left:12px;top:330px;width:396px;list-style:none;font-size:6.4px;line-height:10.5px;font-weight:700;color:var(--navy)}
.ticks li::before{content:"▲ ";color:var(--bright);font-size:5px}
.closing{left:12px;top:400px;width:396px;font-size:7.6px;line-height:9.5px;color:var(--ink);text-align:justify}
.cloud span{position:absolute;color:var(--blue);white-space:nowrap;line-height:1}
.cloud .em{color:var(--navy);font-weight:700}
</style>
</head>
<body>

<section class="page page--consultancy">
  <div class="abs hero-photo" role="img" aria-label="Photo of a team meeting in a bright office with a presenter at a whiteboard"></div>
  <div class="abs brand" style="left:22px;top:44px;font-size:22px"><span class="brand-mark"></span>VELTRANE</div>
  <svg class="abs band" style="top:100px" width="420" height="66" viewBox="0 0 420 66">
    <path d="M0 10 H205 C220 10 225 34 245 34 H420 V62 H0 Z" fill="var(--ink)"/>
    <path d="M150 62 C190 62 205 28 235 28 H420" fill="none" stroke="var(--blue)" stroke-width="3"/>
    <path d="M0 64 H420" stroke="var(--pale)" stroke-width="3"/>
  </svg>
  <p class="abs tagline">A partner who brings new and innovative<br>ideas to the table, through extensive industry<br>experience and knowledge.<br>Veltrane will ensure you are prepared for growth.</p>
  <div class="abs phone" style="right:12px;top:138px">+44 (0) 7700 900123</div>

  <h2 class="abs heading" style="left:12px;top:190px">VELTRANE CONSULTANCY</h2>
  <p class="abs small" style="left:12px;top:210px;width:396px">Veltrane is a bespoke consultancy firm that specialises in buy side investment. Through an industry based consultative approach we assist our clients in preparing for and facilitating long term growth. Working closely with our clients we combine innovative thinking and breakthrough technologies to accelerate progress and, together, achieve enduring results.</p>
  <p class="abs small" style="left:12px;top:233px;width:396px">Experienced in successfully delivering change for global organisations as well as assisting smaller firms during their growth phase. Veltrane will work with you to create a workable model and ensure successful delivery of the project.</p>

  <svg class="abs" style="left:0;top:262px" width="420" height="30" viewBox="0 0 420 30">
    <path d="M30 26 V12 Q30 6 36 6 H394 Q400 6 400 12 V26" fill="none" stroke="var(--navy)" stroke-width="1"/>
    <path d="M27 23 L30 28 L33 23 M397 23 L400 28 L403 23" fill="none" stroke="var(--navy)" stroke-width="1"/>
  </svg>

  <div class="abs services">
    <div class="service"><div class="service-dot"><svg viewBox="0 0 12 12"><rect x="2" y="2" width="8" height="8" fill="none" stroke="#fff"/><path d="M4 5H8M4 7H8" stroke="#fff"/></svg></div>Order Management and Trading</div>
    <div class="service"><div class="service-dot"><svg viewBox="0 0 12 12"><rect x="2" y="2" width="8" height="8" fill="none" stroke="#fff"/><path d="M4 9V6M6 9V4M8 9V5" stroke="#fff"/></svg></div>Investment and Research</div>
    <div class="service"><div class="service-dot"><svg viewBox="0 0 12 12"><rect x="2" y="3" width="8" height="6" fill="none" stroke="#fff"/><path d="M3 8L5 6L7 7L9 4" fill="none" stroke="#fff"/></svg></div>Static, Pricing and Benchmark Data</div>
    <div class="service"><div class="service-dot"><svg viewBox="0 0 12 12"><rect x="1.5" y="3" width="9" height="6" fill="none" stroke="#fff"/><path d="M3 6H9" stroke="#fff"/></svg></div>CRM/Onboarding</div>
    <div class="service"><div class="service-dot"><svg viewBox="0 0 12 12"><path d="M2 8A4 4 0 0 1 10 8" fill="none" stroke="#fff"/><path d="M6 8L8 5" stroke="#fff"/></svg></div>Performance, Risk and Attribution</div>
    <div class="service"><div class="service-dot"><svg viewBox="0 0 12 12"><rect x="3" y="1.5" width="6" height="9" fill="none" stroke="#fff"/><path d="M4.5 4H7.5M4.5 6H7.5M4.5 8H6.5" stroke="#fff"/></svg></div>Client and Regulatory Reporting</div>
    <div class="service"><div class="service-dot"><svg viewBox="0 0 12 12"><circle cx="6" cy="6" r="4" fill="none" stroke="#fff"/><path d="M4 6L5.5 7.5L8 4.5" fill="none" stroke="#fff"/></svg></div>Compliance</div>
    <div class="service"><div class="service-dot"><svg viewBox="0 0 12 12"><rect x="2.5" y="1.5" width="7" height="9" fill="none" stroke="#fff"/><path d="M4 4H8M4 6H5M6 6H7M4 8H5M6 8H7" stroke="#fff"/></svg></div>Finance and Accounting</div>
    <div class="service"><div class="service-dot"><svg viewBox="0 0 12 12"><rect x="1.5" y="3" width="9" height="6" fill="none" stroke="#fff"/><circle cx="6" cy="6" r="1.5" fill="none" stroke="#fff"/></svg></div>Middle and Back Office</div>
  </div>

  <div class="abs section" style="left:12px;top:360px">
    <h3>BUSINESS STRATEGY</h3>
    <p class="small">Veltrane will help you create a business strategy tailored to your requirements. Ensuring each business process is defined and taken into account allows for a successful design. Creating and implementing an operating model that takes into account budget, resources, culture and your company's vision.</p>
  </div>
  <div class="abs section" style="left:218px;top:360px">
    <h3>CHANGE MANAGEMENT</h3>
    <p class="small">Veltrane works with clients to deliver bespoke change initiatives. Rigorous business analysis and risk management allows for successful change initiatives. We work with you throughout the complete process, to ensure that delivery is based on value. Transition phases are challenging aspects of change initiatives which is why our team manage all transitions and the risk they carry.</p>
  </div>
  <div class="abs section" style="left:12px;top:445px">
    <h3>IT TRANSFORMATION</h3>
    <p class="small">Veltrane is widely experienced in a range of technologies. We help with the implementation of software provider or design and develop bespoke services. Covering front to back office the team specialises in full project lifecycle from feasibility through to implementation.</p>
  </div>
  <div class="abs section" style="left:218px;top:445px">
    <h3>ORGANISATIONAL STRUCTURE</h3>
    <p class="small">Veltrane works with clients to improve resource capability and strategic partnerships. Acting as an extension of the HR function, we analyse business processes and ensure that our clients have the ability to manage changing workforce demands.</p>
  </div>

  <svg class="abs web-bar" width="420" height="47" viewBox="0 0 420 47">
    <rect x="0" y="22" width="420" height="25" fill="var(--pale)"/>
    <path d="M0 0 H205 L222 22 H0 Z" fill="var(--navy)"/>
  </svg>
  <div class="abs web">www.veltranepartners.com</div>
  <div class="abs contact"><span class="contact-dot"></span>London, United Kingdom | info@veltranepartners.com</div>
</section>

<section class="page page--recruitment">
  <svg class="abs band" width="420" height="96" viewBox="0 0 420 96">
    <path d="M0 0 H420 V90 H260 C235 90 230 70 210 70 H0 Z" fill="var(--ink)"/>
    <path d="M130 72 H205 C228 72 235 88 262 88 H420" fill="none" stroke="var(--blue)" stroke-width="3"/>
    <path d="M0 94 H420" stroke="var(--pale)" stroke-width="3"/>
  </svg>
  <div class="abs phone" style="left:12px;top:36px;font-size:13px">+44 (0) 7700 900123</div>
  <div class="abs brand brand--light" style="right:16px;top:40px;font-size:22px"><span class="brand-mark"></span>VELTRANE</div>

  <h2 class="abs heading" style="left:12px;top:100px">VELTRANE RECRUITMENT</h2>
  <p class="abs intro">A partner who brings new and innovative ideas to the table, through extensive industry experience and knowledge. Veltrane will ensure you are prepared for growth.</p>
  <p class="abs small" style="left:12px;top:145px;width:396px">Veltrane is more than an ordinary recruitment service. Our experts work with clients to develop a HR strategy that maps current and impending organisational needs, using research to effectively benchmark. We are developing various talent communities that provide effective and timely recruitment solutions for our clients.</p>
  <p class="abs small" style="left:12px;top:172px;width:396px">Specialists in Asset Management recruitment with a specialisation in IT, Operations, Regulation and Change Management.</p>
  <p class="abs small" style="left:12px;top:186px;width:396px">Veltrane acts as an extension of your HR function, providing an end-to-end permanent and contingent talent acquisition solution, taking full accountability and ownership for the entire recruitment process.</p>

  <div class="abs pill">▲ Workforce Planning &nbsp;▲ Strategic Sourcing &nbsp;▲ Talent Engagement<br>▲ Candidate Management &nbsp;▲ Weekly Vacancy Updates</div>

  <p class="abs small" style="left:12px;top:300px;width:396px">We recognise that hiring can be a lengthy process, therefore we partner with you to ensure you only interview top quartile candidates, cutting out multiple meetings with multiple candidates. Giving hiring managers time back in their diaries to do their day jobs and reducing the time to hire.</p>

  <ul class="abs ticks">
    <li>Understanding the roles, and partnering with you to build meaningful job descriptions</li>
    <li>Candidates are fully screened and interviewed prior to presentation to you</li>
    <li>Qualified shortlist of top 3 candidates</li>
    <li>Support with interviews and we ensure the candidate has a positive experience</li>
  </ul>

  <p class="abs closing">Veltrane recruitment partners with principal business consultants from Veltrane consultancy to ensure candidates are properly screened before presenting to our clients. This allows for our clients to focus on only interviewing the best on the market.</p>

  <div class="abs cloud" style="left:0;top:445px;width:420px;height:90px">
    <span style="left:40px;top:8px;font-size:10px">Pricing and</span>
    <span style="left:46px;top:18px;font-size:10px">Analytics</span>
    <span style="left:102px;top:4px;font-size:24px" class="em">XML</span>
    <span style="left:162px;top:6px;font-size:11px">Fixed Income</span>
    <span style="left:232px;top:0px;font-size:22px" class="em">MIS</span>
    <span style="left:28px;top:34px;font-size:8px">Connectivity</span>
    <span style="left:76px;top:33px;font-size:9px">Reference Data</span>
    <span style="left:176px;top:44px;font-size:8px;transform:rotate(-90deg);transform-origin:left top">Equity</span>
    <span style="left:186px;top:24px;font-size:20px" class="em">SQL</span>
    <span style="left:232px;top:25px;font-size:9px">Workflow Management</span>
    <span style="left:240px;top:35px;font-size:9.5px">Collateral</span>
    <span style="left:32px;top:47px;font-size:11px">Business Intelligence</span>
    <span style="left:186px;top:45px;font-size:13px">Orvanta</span>
    <span style="left:232px;top:47px;font-size:9.5px">Management</span>
    <span style="left:20px;top:64px;font-size:10px">Settlement Risk and attribution</span>
    <span style="left:166px;top:60px;font-size:15px" class="em">FIX/Relay</span>
    <span style="left:240px;top:61px;font-size:8px">Batch</span>
    <span style="left:240px;top:69px;font-size:8px">Processing</span>
  </div>

  <svg class="abs web-bar" width="420" height="47" viewBox="0 0 420 47">
    <rect x="0" y="22" width="420" height="25" fill="var(--pale)"/>
    <path d="M0 0 H205 L222 22 H0 Z" fill="var(--navy)"/>
  </svg>
  <div class="abs web">www.veltranepartners.com</div>
  <div class="abs contact"><span class="contact-dot"></span>London, United Kingdom | info@veltranepartners.com</div>
</section>

</body>
</html>
```